Website for Excavator and Earthworks Company

We require a modern, sleek and practical website for our newly created earthworks/excavator business in Perth, Western Australia called Bluegum Ridge Earthworks.

The website should have a modern, cutting edge feel but only needs to be relatively simplistic in it's layout and eventual functionality.

Some pages it should have would be Home, About, Projects and Contact Us.

```html
<!DOCTYPE html>
<html lang="en">
<head>
<meta charset="utf-8">
<title>Bluegum Ridge Earthworks</title>
<link rel="stylesheet" href="https://fonts.googleapis.com/css2?family=Unbounded:wght@800&family=Lato:wght@400;700;800;900&family=Roboto:wght@500&display=swap">
<style>
:root{
  --lime:#c5d900;
  --ink:#111111;
  --text:#555555;
  --grey:#e8e8e6;
  --footer:#1b1b1a;
  --white:#ffffff;
  --display:"Unbounded",sans-serif;
  --body:"Lato",sans-serif;
}
*{box-sizing:border-box;margin:0;padding:0}
html,body{width:1200px;height:4029px;overflow:hidden}
body{position:relative;background:var(--white);font-family:var(--body);color:var(--ink)}
.abs{position:absolute}
.photo{position:absolute}
.btn{position:absolute;display:flex;align-items:center;padding-left:16px;background:var(--lime);color:var(--ink);font-weight:700;font-size:16px;clip-path:polygon(0 0,86% 0,100% 50%,86% 100%,0 100%)}
.brand{display:flex;align-items:center;gap:12px;font-family:var(--body);font-weight:900;font-size:24px;line-height:1.05;letter-spacing:1px;text-transform:uppercase}
.brand-mark{width:44px;height:44px;background:var(--lime);flex:none}
/* header */
.site-header{position:absolute;left:0;top:0;width:1200px;height:80px;background:var(--white)}
.site-header .brand{position:absolute;left:110px;top:14px;color:var(--ink);font-size:20px}
.nav a{position:absolute;top:24px;font-size:16px;color:var(--ink);text-decoration:none}
.nav .active{left:676px;top:18px;height:36px;width:72px;padding:8px 0 0 15px;background:var(--ink);color:var(--white);font-weight:700;clip-path:polygon(0 0,86% 0,100% 50%,86% 100%,0 100%)}
.nav .contact{left:971px;top:17px;width:116px;height:47px;padding:14px 0 0 22px;background:var(--lime);font-weight:700;clip-path:polygon(0 0,86% 0,100% 50%,86% 100%,0 100%)}
/* hero */
.hero-photo{left:0;top:80px;width:1200px;height:622px;background:linear-gradient(180deg,#4f6c88 0%,#8ea2b0 40%,#b58a5e 70%,#7a4a2a 100%)}
.hero-title{left:110px;top:222px;font-family:var(--display);font-size:41px;line-height:58px;color:var(--white);text-transform:uppercase}
.hero-title .lime{color:var(--lime)}
.hero-lead{left:110px;top:468px;font-size:20px;line-height:32px;color:var(--white)}
/* section headings */
.sec-title{position:absolute;left:0;width:1200px;text-align:center;font-family:var(--display);font-size:40px}
.lime{color:var(--lime)}
.eyebrow{position:absolute;display:flex;align-items:center;gap:16px;font-size:17px;font-weight:700;letter-spacing:.5px}
.eyebrow::before,.eyebrow::after{content:"";width:82px;height:3px;background:var(--lime)}
/* services */
.card{position:absolute;top:904px;width:316px;height:402px;background:var(--white);box-shadow:0 2px 10px rgba(0,0,0,.15)}
.card .photo{left:9px;top:10px;width:298px;height:324px}
.card h3{position:absolute;left:0;width:100%;top:354px;text-align:center;font-weight:500;font-size:22px;font-family:var(--body)}
.card.featured{background:var(--lime)}
.card.featured .photo{clip-path:polygon(0 0,100% 0,100% 82%,50% 100%,0 82%)}
.card.featured .icon{position:absolute;left:133px;top:208px;width:50px;height:50px;border-radius:50%;background:var(--lime);display:flex;align-items:center;justify-content:center}
.card.featured h3{top:290px}
.card.featured p{position:absolute;top:327px;width:100%;text-align:center;font-size:14px;color:#4d5300}
.arrow-dot{position:absolute;width:26px;height:26px;border-radius:50%;display:flex;align-items:center;justify-content:center}
/* why */
.why-band{left:0;top:1403px;width:1200px;height:481px;background:var(--grey)}
.why-photo{left:0;top:1403px;width:670px;height:470px;background:linear-gradient(135deg,#6d8fa8,#c7a143 55%,#3e4a3a);clip-path:polygon(0 0,100% 0,86% 100%,0 100%)}
.benefit{position:absolute;left:713px;display:flex;align-items:center;gap:21px;font-size:16px;color:#4a4a4a}
.benefit .ic{width:44px;height:44px;border-radius:50%;background:var(--lime);display:flex;align-items:center;justify-content:center}
/* about */
.about-copy{left:111px;top:2100px;width:442px;font-size:13.5px;line-height:27.5px;color:var(--text);text-align:justify}
.about-copy p+p{margin-top:10px}
/* cta */
.cta{left:110px;top:2502px;width:980px;height:428px;background:linear-gradient(180deg,#1e4f96 0%,#5f86b6 45%,#8a7a5a 75%,#5a4a36 100%)}
.cta h2{position:absolute;left:0;width:100%;top:138px;text-align:center;font-family:var(--display);font-size:40px;line-height:58px;color:var(--white)}
.cta p{position:absolute;left:0;width:100%;top:252px;text-align:center;color:var(--white);font-size:17px;font-weight:700}
/* gallery */
.g{position:absolute}
.caption{left:102px;top:3126px;width:444px;height:415px;background:linear-gradient(180deg,rgba(197,217,0,0) 55%,rgba(197,217,0,.95) 90%)}
.caption span{position:absolute;left:50px;bottom:22px;font-family:"Roboto",sans-serif;font-weight:500;font-size:26px}
/* footer */
.site-footer{left:0;top:3645px;width:1200px;height:384px;background:var(--footer);color:var(--white)}
.site-footer .brand{position:absolute;left:102px;top:82px;color:var(--white);font-size:20px}
.email{position:absolute;left:111px;top:158px;width:341px;height:50px;background:var(--white);padding:15px 14px;color:#666;font-size:13px}
.col h4{position:absolute;top:89px;font-size:19px;font-weight:800;color:var(--lime)}
.col a{position:absolute;font-size:13px;color:var(--white);text-decoration:none}
.social{position:absolute;top:305px;width:22px;height:22px;background:var(--lime)}
.contact-row{position:absolute;left:889px;display:flex;align-items:center;gap:17px;font-size:13px}
.contact-row .ic{width:22px;height:22px;border-radius:4px;background:var(--white);display:flex;align-items:center;justify-content:center}
.rule{position:absolute;left:102px;top:340px;width:984px;height:1px;background:#666}
.copy{position:absolute;left:0;width:1200px;top:355px;text-align:center;font-size:15px}
</style>
</head>
<body>

<header class="site-header">
  <div class="brand"><span class="brand-mark"></span><span>Bluegum Ridge<br>Earthworks</span></div>
  <nav class="nav">
    <a class="active" href="#">Home</a>
    <a href="#" style="left:777px">About</a>
    <a href="#" style="left:867px">Projects</a>
    <a class="contact" href="#">CONTACT</a>
  </nav>
</header>

<section>
  <div class="photo hero-photo" role="img" aria-label="Yellow excavator digging red earth under a cloudy sky"></div>
  <h1 class="abs hero-title">Reliable<br><span class="lime">Excavation &amp;<br>Earth Moving</span><br>Solutions</h1>
  <p class="abs hero-lead">Precision excavation, site preparation and<br>earthmoving solutions across Western Australia.</p>
  <a class="btn" style="left:108px;top:549px;width:134px;height:46px;font-size:15px">GET A QUOTE</a>
</section>

<section>
  <h2 class="sec-title" style="top:782px">What <span class="lime">We Do</span></h2>
  <div class="eyebrow" style="left:463px;top:849px">SERVICES</div>
  <div class="arrow-dot" style="left:34px;top:1099px;background:var(--lime)"><svg width="12" height="12" viewBox="0 0 12 12"><path d="M8 2 4 6l4 4" stroke="#fff" stroke-width="2" fill="none"/></svg></div>
  <div class="card" style="left:111px"><div class="photo" role="img" aria-label="Two workers walking in an open-pit mine with dump trucks" style="background:linear-gradient(180deg,#8fa0ad,#5b5e5c 50%,#3d3f3e)"></div><h3>Excavation</h3></div>
  <div class="card featured" style="left:441px"><div class="photo" role="img" aria-label="Excavator laying large drainage pipe in a trench" style="background:linear-gradient(180deg,#4b86c4,#b3906a 55%,#7b5a3c)"></div>
    <div class="icon"><svg width="26" height="26" viewBox="0 0 26 26" fill="none" stroke="#111" stroke-width="2"><rect x="5" y="4" width="6" height="10"/><circle cx="18" cy="9" r="5"/><path d="M3 19c3 2 6 2 10 0s7-2 10 0"/></svg></div>
    <h3>Trenching &amp; Drainage</h3><p>Utility trenches and drainage systems.</p></div>
  <div class="card" style="left:770px"><div class="photo" role="img" aria-label="Excavator clearing trees and scrub" style="background:linear-gradient(180deg,#5f92c9,#6f8a5a 45%,#a07a4e)"></div><h3>Land Clearing</h3></div>
  <div class="arrow-dot" style="left:1123px;top:1099px;background:#cfcfcf"><svg width="12" height="12" viewBox="0 0 12 12"><path d="M4 2l4 4-4 4" stroke="#fff" stroke-width="2" fill="none"/></svg></div>
</section>

<section>
  <div class="abs why-band"></div>
  <div class="photo why-photo" role="img" aria-label="Smiling operator in hard hat giving a thumbs up from an excavator cab"></div>
  <svg class="abs" style="left:570px;top:1470px" width="90" height="410"><line x1="83" y1="5" x2="6" y2="405" stroke="var(--lime)" stroke-width="6"/></svg>
  <h2 class="abs" style="left:706px;top:1462px;font-family:var(--display);font-size:40px">Why <span class="lime">Choose Us</span></h2>
  <div class="eyebrow" style="left:714px;top:1528px">BENEFITS</div>
  <div class="benefit" style="top:1574px"><span class="ic"><svg width="20" height="20" viewBox="0 0 20 20"><rect x="3" y="10" width="12" height="5" fill="#111"/><path d="M9 10V5l6-2" stroke="#111" stroke-width="2" fill="none"/></svg></span>Modern Equipment Fleet</div>
  <div class="benefit" style="top:1629px"><span class="ic"><svg width="20" height="20" viewBox="0 0 20 20" fill="#111"><circle cx="10" cy="6" r="4"/><path d="M3 18c0-5 14-5 14 0z"/></svg></span>Experienced Operators</div>
  <div class="benefit" style="top:1685px"><span class="ic"><svg width="20" height="20" viewBox="0 0 20 20"><path d="M10 2l7 3v5c0 4-3 7-7 8-4-1-7-4-7-8V5z" fill="#111"/><path d="M7 10l2 2 4-4" stroke="#c5d900" stroke-width="2" fill="none"/></svg></span>Safety Focused</div>
  <div class="benefit" style="top:1746px"><span class="ic"><svg width="20" height="20" viewBox="0 0 20 20" fill="none" stroke="#111" stroke-width="2"><circle cx="10" cy="10" r="7"/><path d="M10 6v4l3 2"/></svg></span>Reliable Scheduling</div>
  <div class="benefit" style="top:1799px"><span class="ic"><svg width="20" height="20" viewBox="0 0 20 20"><path d="M3 10l7-7h6v6l-7 7z" fill="#111"/><circle cx="13" cy="7" r="1.5" fill="#c5d900"/></svg></span>Competitive Pricing</div>
</section>

<section>
  <h2 class="abs" style="left:113px;top:1992px;font-family:var(--display);font-size:40px">Who <span class="lime">We Are</span></h2>
  <div class="eyebrow" style="left:113px;top:2057px">ABOUT US</div>
  <div class="abs about-copy">
    <p>At Bluegum Ridge Earthworks, we treat every project as a reflection of our reputation. We are committed to delivering clean job sites, precise results, and dependable service from the first consultation to final handover.</p>
    <p>Our mission is simple — to deliver dependable earthmoving solutions while building long-term relationships based on trust, performance, and quality workmanship.</p>
  </div>
  <a class="btn" style="left:111px;top:2325px;width:134px;height:46px">READ MORE</a>
  <div class="photo" role="img" aria-label="Two site engineers in hi-vis reviewing plans beside an excavator" style="left:745px;top:1999px;width:344px;height:415px;background:linear-gradient(180deg,#b9b4aa,#9a7d5c 55%,#5d4634)"></div>
  <div class="photo" role="img" aria-label="Excavator bucket lifting soil against a blue sky" style="left:643px;top:2169px;width:299px;height:248px;background:linear-gradient(180deg,#6fa3d6,#a9c6e2 45%,#b68554 75%,#8a5d36);border:3px solid var(--white)"></div>
</section>

<section>
  <div class="abs cta" role="img" aria-label="Excavator working on a cleared site under a deep blue sky">
    <h2>Let’s Build Strong<br>Foundations Together</h2>
    <p>From First Dig To Final Grade — We’ve Got You Covered</p>
  </div>
  <a class="btn" style="left:515px;top:2803px;width:166px;height:45px">BOOK YOUR JOB</a>
</section>

<section>
  <h2 class="sec-title" style="top:3005px">Our <span class="lime">Projects</span></h2>
  <div class="eyebrow" style="left:461px;top:3064px">GALLERY</div>
  <div class="g" role="img" aria-label="Aerial view of excavators working in a sandy pit" style="left:102px;top:3126px;width:444px;height:415px;background:linear-gradient(160deg,#b9b39e,#9d8f73 50%,#b7a88a)"></div>
  <div class="g caption"><span>Lorm Ipsum Dolor Siet</span></div>
  <div class="g" role="img" aria-label="Small excavator digging in a suburban garden" style="left:577px;top:3126px;width:218px;height:202px;background:linear-gradient(180deg,#9cc1df,#7a8e5a 55%,#5e7a3a)"></div>
  <div class="g" role="img" aria-label="Excavator at a hillside building site" style="left:809px;top:3126px;width:277px;height:202px;background:linear-gradient(180deg,#8db7db,#5e7e4a 45%,#8a7a5e)"></div>
  <div class="g" role="img" aria-label="Excavator clearing a pine forest" style="left:577px;top:3340px;width:277px;height:202px;background:linear-gradient(180deg,#c9d3d6,#3f5a3a 45%,#6a5a3e)"></div>
  <div class="g" role="img" aria-label="Excavator working in dense green bushland" style="left:868px;top:3340px;width:218px;height:202px;background:linear-gradient(180deg,#5f7e3a,#8aa44a 50%,#6a5a2e)"></div>
</section>

<footer class="abs site-footer">
  <div class="brand"><span class="brand-mark"></span><span>Bluegum Ridge<br>Earthworks</span></div>
  <div class="email">Enter email address</div>
  <a class="btn" style="left:111px;top:222px;width:136px;height:47px">SUBSCRIBE</a>
  <span class="social" style="left:114px" aria-label="Social link"></span>
  <span class="social" style="left:150px" aria-label="Social link"></span>
  <span class="social" style="left:186px" aria-label="Social link"></span>
  <span class="social" style="left:223px" aria-label="Social link"></span>
  <div class="col"><h4 style="left:525px">Quick Links</h4>
    <a style="left:526px;top:130px">Home</a><a style="left:526px;top:161px">About Us</a><a style="left:526px;top:192px">Service</a><a style="left:526px;top:223px">Projects</a><a style="left:526px;top:253px">Contact Us</a></div>
  <div class="col"><h4 style="left:705px">Other Links</h4>
    <a style="left:706px;top:130px">Privacy Policy</a><a style="left:706px;top:161px">Terms &amp; Conditions</a><a style="left:706px;top:192px">FAQ’s</a><a style="left:706px;top:223px">Suport</a><a style="left:706px;top:253px">Help</a></div>
  <div class="col"><h4 style="left:889px">Contact Info</h4></div>
  <div class="contact-row" style="top:144px"><span class="ic"><svg width="12" height="14" viewBox="0 0 12 14"><path d="M6 1a4.5 4.5 0 0 0-4.5 4.5C1.5 9 6 13 6 13s4.5-4 4.5-7.5A4.5 4.5 0 0 0 6 1z" fill="#111"/><circle cx="6" cy="5.5" r="1.6" fill="#fff"/></svg></span>Lorem Ipsum,USA-437916</div>
  <div class="contact-row" style="top:199px"><span class="ic"><svg width="12" height="12" viewBox="0 0 12 12"><path d="M2 1h3l1 3-2 1a7 7 0 0 0 3 3l1-2 3 1v3c-6 0-9-3-9-9z" fill="#111"/></svg></span>+1 888 888 8888</div>
  <div class="contact-row" style="top:254px"><span class="ic"><svg width="12" height="10" viewBox="0 0 12 10"><rect x="0.5" y="0.5" width="11" height="9" fill="none" stroke="#111"/><path d="M1 1l5 4 5-4" stroke="#111" fill="none"/></svg></span>bluegumridgeearthworks.com.au</div>
  <div class="rule"></div>
  <p class="copy">© 2026 &nbsp; Bluegum Ridge Earthworks. All rights reserved.</p>
</footer>

</body>
</html>
```